KAJU Freightways #ALLKAJU Business Cards & Letterhead

I am looking to business cards designed for our organization. We are currently undergoing a small re-branding that is taking place. Our organization is called KAJU Freightways and we are headquartered in Phoenix, AZ. We primarily provide transportation and logistics services to the Marlow Parcel Bureau who is our largest customer. I would like to see a design that incorporates name, title, contact info, website, and address (this will be different depending on the employee). I would also like to see some color on the business card using our logo colors or a variation. I would like our logo on the back of the business card with the website displayed. The final design should communicate that we are a next generation transportation operate that focuses on being driver-first, customer-centric, innovative, and sustainable.We would also like our #ALLKAJU catch phrase incorporated as well.

Target Market(s)

Transportation & Logistics

Industry/Entity Type

Trucking Company

Contact Information for Business Card

-First and Last Name
-Position Title
-Contact Phone
-Contact Email
-Physical Address

Font styles to use
Serif

Colors

Designer to choose colors to be used in the design.

Requirements
Must have
• -KAJU logo prominently displayed
• -#ALLKAJU catch phrase used
• -Some amount of color, design gradient, etc.
• -Logo on the back with website listed (https://www.kajufreightco.example)

```html
<!DOCTYPE html>
<html lang="en">
<head>
<meta charset="utf-8">
<title>KAJU Freightways — Business Cards</title>
<link rel="stylesheet" href="https://fonts.googleapis.com/css2?family=Montserrat:wght@400;500;700;800&display=swap">
<style>
  :root {
    --teal-deep: #113a47;
    --teal-mid: #1b4f5e;
    --teal-soft: #245d6d;
    --green: #7cc242;
    --ink-grey: #6e7478;
    --paper: #ffffff;
    --stage: #2a2d31;
  }
  * { margin: 0; padding: 0; box-sizing: border-box; }
  html, body { width: 1200px; height: 900px; overflow: hidden; }
  body {
    background: var(--stage);
    font-family: "Montserrat", Arial, sans-serif;
    position: relative;
  }
  .card {
    position: absolute;
    left: 250px;
    width: 700px;
    height: 400px;
    overflow: hidden;
    border-radius: 4px;
  }
  .card-back { top: 35px; background: linear-gradient(135deg, var(--teal-deep), var(--teal-mid)); }
  .card-front { top: 465px; background: var(--paper); }

  .card-art { position: absolute; inset: 0; width: 100%; height: 100%; }

  .brand-word {
    position: absolute;
    font-family: "Montserrat", Arial, sans-serif;
    font-weight: 700;
    color: var(--paper);
    text-align: center;
    line-height: 1;
  }
  .card-back .brand-word { left: 300px; top: 112px; width: 330px; font-size: 60px; letter-spacing: 2px; }
  .card-front .brand-word { left: 410px; top: 182px; width: 260px; font-size: 64px; letter-spacing: 2px; }

  .back-lockup {
    position: absolute;
    left: 300px;
    top: 200px;
    width: 330px;
    text-align: center;
    color: var(--paper);
  }
  .back-lockup .brand-name {
    font-weight: 700;
    font-size: 22px;
    letter-spacing: 3px;
  }
  .back-lockup .brand-site {
    margin-top: 18px;
    font-size: 17px;
    font-weight: 400;
    letter-spacing: 0.5px;
  }
  .brand-site strong { color: var(--green); font-weight: 700; }

  .contact-block {
    position: absolute;
    left: 46px;
    top: 44px;
    width: 300px;
  }
  .person-name {
    font-weight: 800;
    font-size: 24px;
    color: var(--teal-deep);
    letter-spacing: 0.5px;
  }
  .person-title {
    font-size: 16px;
    color: var(--teal-mid);
    margin-top: 2px;
  }
  .contact-list { list-style: none; margin-top: 24px; }
  .contact-list li {
    display: flex;
    align-items: center;
    gap: 10px;
    font-size: 16px;
    color: var(--ink-grey);
    line-height: 26px;
    white-space: nowrap;
  }
  .contact-list svg { width: 15px; height: 15px; flex: none; }
  .address {
    margin-top: 10px;
    font-size: 16px;
    color: var(--ink-grey);
    line-height: 24px;
  }
  .tagline {
    margin-top: 18px;
    display: flex;
    align-items: center;
    gap: 12px;
    color: var(--green);
    font-size: 18px;
    font-weight: 500;
  }
  .tagline::before {
    content: "";
    width: 12px;
    height: 4px;
    background: var(--green);
  }
</style>
</head>
<body>

<section class="card card-back" aria-label="Business card back">
  <svg class="card-art" viewBox="0 0 700 400" aria-hidden="true">
    <circle cx="465" cy="175" r="300" fill="none" stroke="var(--teal-soft)" stroke-opacity="0.35" stroke-width="26"/>
    <circle cx="465" cy="175" r="230" fill="var(--teal-deep)" fill-opacity="0.35"/>
  </svg>
  <div class="brand-word">KAJU</div>
  <div class="back-lockup">
    <div class="brand-name">FREIGHTWAYS</div>
    <div class="brand-site">www.<strong>kajufreightco</strong>.example</div>
  </div>
</section>

<section class="card card-front" aria-label="Business card front">
  <svg class="card-art" viewBox="0 0 700 400" aria-hidden="true">
    <path d="M700 0 H540 A180 180 0 0 0 360 180 V400 H700 Z" fill="var(--teal-deep)"/>
    <path d="M342 250 A200 200 0 0 1 530 -6" fill="none" stroke="var(--green)" stroke-width="5" stroke-linecap="round"/>
  </svg>
  <div class="brand-word">KAJU</div>

  <div class="contact-block">
    <h1 class="person-name">DANA ROURKE</h1>
    <p class="person-title">Chairman &amp; CEO</p>
    <ul class="contact-list">
      <li>
        <svg viewBox="0 0 16 16"><circle cx="8" cy="8" r="7" fill="none" stroke="var(--green)" stroke-width="1.5"/><path d="M5.5 4.5 L7 6.5 L6.2 7.6 Q7.2 9.2 8.6 9.9 L9.7 9.1 L11.6 10.6 L10.8 11.8 Q6.2 11.3 4.4 5.5 Z" fill="var(--green)"/></svg>
        555-014-0192
      </li>
      <li>
        <svg viewBox="0 0 16 16"><rect x="1.5" y="3.5" width="13" height="9" fill="none" stroke="var(--green)" stroke-width="1.5"/><path d="M1.5 3.5 L8 9 L14.5 3.5" fill="none" stroke="var(--green)" stroke-width="1.5"/></svg>
        info@kajufreightco.example
      </li>
      <li>
        <svg viewBox="0 0 16 16"><circle cx="8" cy="8" r="6.5" fill="none" stroke="var(--green)" stroke-width="1.5"/><ellipse cx="8" cy="8" rx="3" ry="6.5" fill="none" stroke="var(--green)" stroke-width="1.2"/><path d="M1.5 8 H14.5" stroke="var(--green)" stroke-width="1.2"/></svg>
        www.kajufreightco.example
      </li>
    </ul>
    <p class="address">4410 Cinder Ridge<br>Parkway, Mesa Verde, AZ 85000</p>
    <p class="tagline">#ALLKAJU</p>
  </div>
</section>

</body>
</html>
```